Fenwick Ridge Accounting - New client package

I need a stationary package (presentation folder cover, welcome letter template/design, sample financial report template/design, business card and new logo) for my accounting business. I would like to see designs that use the color blue. Financial icons can be included in the design. The final design should be clean and communicate professionalism and the use of modern; user-friendly technology. Attached postcard files should help with overall design concept.

```html
<!DOCTYPE html>
<html lang="en">
<head>
<meta charset="utf-8">
<title>Fenwick Ridge Accounting – Stationery</title>
<link rel="stylesheet" href="https://fonts.googleapis.com/css2?family=Montserrat:wght@400;500&family=Arimo:wght@400;700&display=swap">
<style>
:root{
  --backdrop:#d4d4d9;
  --navy:#0b5196;
  --navy-deep:#0a4687;
  --sky:#1b95d0;
  --paper:#ffffff;
  --ink:#2a2a2a;
  --muted:#444;
}
*{box-sizing:border-box;margin:0;padding:0}
html,body{width:1200px;height:1041px;overflow:hidden;background:var(--backdrop)}
.canvas{position:relative;width:1200px;height:1041px;font-family:"Arimo",Arial,sans-serif;color:var(--ink)}
.sheet{position:absolute;background:var(--paper);overflow:hidden}
.brand{font-family:"Montserrat",Arial,sans-serif;font-weight:400;color:var(--navy);letter-spacing:.04em;text-transform:uppercase;line-height:1.05;display:flex;align-items:center}
.brand .mark{display:block;background:var(--navy);flex:none}
.brand.on-dark{color:#fff}
.brand.on-dark .mark{background:#fff}
.stripe{position:absolute;left:0;bottom:0;width:100%;display:block}

/* folder */
.folder{left:165px;top:76px;width:418px;height:541px;background:var(--navy);border-radius:3px}
.folder .spine{position:absolute;left:24px;top:0;width:3px;height:100%;background:var(--navy-deep)}
.folder .cover-brand{position:absolute;left:0;right:0;top:200px;justify-content:center;flex-direction:column;gap:12px;font-size:19px;text-align:center}
.folder .cover-brand .mark{width:22px;height:22px}
.folder .cover-name{position:absolute;left:0;right:0;top:464px;text-align:center;font-family:"Montserrat",Arial,sans-serif;color:#fff;font-size:19px;letter-spacing:.04em}

/* letter */
.letter{left:615px;top:95px;width:403px;height:523px}
.letter .brand{position:absolute;left:30px;top:37px;font-size:10px;gap:7px}
.letter .brand .mark{width:12px;height:12px}
.contact{position:absolute;font-size:5px;line-height:7px;color:var(--muted)}
.letter .contact{left:294px;top:37px}
.contact .row{display:flex;align-items:center;gap:3px}
.contact svg{width:5px;height:5px;fill:var(--navy)}
.contact .gap{height:4px}
.letter .recipient{position:absolute;left:30px;top:110px;font-size:5.4px;line-height:7px}
.letter .body{position:absolute;left:30px;top:168px;width:344px;font-size:5.1px;line-height:7px;text-align:justify}
.letter .body p{margin-bottom:7px}
.letter .salutation{font-weight:700;margin-bottom:7px}
.letter .signature{position:absolute;left:30px;top:362px;width:68px;height:28px;background:linear-gradient(90deg,#e9e9f4,#f4f4fa);border-radius:3px}
.letter .signoff{position:absolute;left:30px;top:346px;font-size:5.4px}
.letter .signer{position:absolute;left:30px;top:396px;font-size:5.4px;line-height:7px}
.letter .signer b{font-weight:700}

/* envelopes */
.envelope-front{left:132px;top:645px;width:451px;height:196px}
.envelope-front .brand{position:absolute;left:23px;top:22px;font-size:8.4px;gap:6px}
.envelope-front .brand .mark{width:10px;height:10px}
.envelope-front .return{position:absolute;left:23px;top:163px;font-size:5px;line-height:7px;color:var(--muted)}
.envelope-back{left:615px;top:645px;width:451px;height:196px}
.envelope-back .flap{position:absolute;left:0;top:0;width:451px;height:62px;display:block}
.envelope-back .brand{position:absolute;left:0;right:0;top:24px;justify-content:center;font-size:6px;gap:5px}
.envelope-back .brand .mark{width:7px;height:7px}

/* cards */
.card-front{left:417px;top:870px;width:167px;height:95px}
.card-front .brand{position:absolute;left:12px;top:14px;font-size:5.6px;gap:4px}
.card-front .brand .mark{width:7px;height:7px}
.card-front .person{position:absolute;right:12px;top:14px;text-align:right}
.card-front .person b{display:block;font-size:5.4px;color:var(--navy);font-weight:700}
.card-front .person span{font-size:3.6px;color:var(--muted)}
.card-front .contact{left:12px;top:66px;font-size:3.6px;line-height:5.4px}
.card-front .contact svg{width:3.6px;height:3.6px}
.card-front .office{position:absolute;right:12px;top:72px;font-size:3.6px;line-height:5.4px;text-align:right;color:var(--muted)}
.card-back{left:615px;top:870px;width:167px;height:95px;background:var(--navy)}
.card-back .brand{position:absolute;left:0;right:0;top:38px;justify-content:center;font-size:6.8px;gap:5px}
.card-back .brand .mark{width:8px;height:8px}
</style>
</head>
<body>
<main class="canvas">

  <section class="sheet folder" aria-label="Presentation folder cover">
    <div class="spine"></div>
    <div class="brand on-dark cover-brand"><span class="mark"></span><span>Fenwick Ridge<br>Accounting</span></div>
    <div class="cover-name">FENWICK RIDGE ACCOUNTING</div>
  </section>

  <section class="sheet letter" aria-label="Letterhead">
    <div class="brand"><span class="mark"></span><span>Fenwick<br>Ridge<br>Accounting</span></div>
    <div class="contact">
      <div>Level 12, Keel Tower</div>
      <div>18 Quay Lane, Sydney</div>
      <div class="gap"></div>
      <div class="row"><svg viewBox="0 0 10 10"><path d="M2 0h2l1 3-1.5 1a6 6 0 0 0 2.5 2.5L7 5l3 1v2a2 2 0 0 1-2 2A8 8 0 0 1 0 2a2 2 0 0 1 2-2z"/></svg>555-014-2290</div>
      <div class="row"><svg viewBox="0 0 10 10"><path d="M0 2h10v6H0zM0 2l5 3.5L10 2" /></svg>info@fenwickridge.com</div>
      <div class="row"><svg viewBox="0 0 10 10"><circle cx="5" cy="5" r="5"/></svg>www.fenwickridge.com</div>
    </div>
    <div class="recipient">
      Mr. Desmond Arklow<br>President and CEO<br>Corvane Systems LLC.<br>880 Halden Avenue, Suite 210<br>Riverton, NY 10099
    </div>
    <div class="body">
      <p class="salutation">Dear Mr. Arklow:</p>
      <p>As Chairperson of the Corporate Conscience Campaign - Helping the Homeless in Riverton, I am writing this to thank you personally for your company's support in last month's fund-raising effort.</p>
      <p>As I indicated when we spoke on the phone two weeks ago, the campaign was considered a resounding success, raising a total of $1.65 million to-date, significantly exceeding our target of $1 million. Some donations are still trickling in, so we could end up close to a total of $2 million.</p>
      <p>Corvane Systems was an influential leader throughout the entire three-month campaign. In fact, we couldn't have succeeded without the generous support of your company, both financially, and through your organizational and administrative assistance. Your Team Leader, Nadia Ferrell was particularly impressive, going above and beyond what we could have expected of someone performing as a volunteer while continuing on with her day-to-day duties. Please convey my special thanks to Nadia.</p>
      <p>I would also ask you to convey my sincere thanks and congratulations to all of those other people in your company who contributed in any way to the Helping the Homeless Campaign. Please tell them that the sum of their contributions resulted in a major success that they should all be proud of taking part in.</p>
      <p>I believe that the 27 companies that participated in this effort have set a new standard for social responsibility in this community, and have set a powerful example that will inspire other companies and organizations to do the same.</p>
      <p>I look forward to seeing you at the Mayor's special thank you reception next month.</p>
    </div>
    <div class="signoff">Yours sincerely,</div>
    <div class="signature" role="img" aria-label="Handwritten signature"></div>
    <div class="signer"><b>Marcus Hollen</b><br>Fundraising Chair</div>
    <svg class="stripe" width="403" height="6" viewBox="0 0 403 6" preserveAspectRatio="none" aria-hidden="true">
      <polygon points="0,0 264,0 259,6 0,6" fill="var(--sky)"/>
      <polygon points="268,0 403,0 403,6 263,6" fill="var(--navy)"/>
    </svg>
  </section>

  <section class="sheet envelope-front" aria-label="Envelope front">
    <div class="brand"><span class="mark"></span><span>Fenwick<br>Ridge<br>Accounting</span></div>
    <div class="return">Level 12, Keel Tower<br>18 Quay Lane, Sydney</div>
    <svg class="stripe" width="451" height="6" viewBox="0 0 451 6" preserveAspectRatio="none" aria-hidden="true">
      <polygon points="0,0 313,0 308,6 0,6" fill="var(--sky)"/>
      <polygon points="317,0 451,0 451,6 312,6" fill="var(--navy)"/>
    </svg>
  </section>

  <section class="sheet envelope-back" aria-label="Envelope back">
    <svg class="flap" viewBox="0 0 451 62" aria-hidden="true">
      <path d="M0 0H451L445 40Q442 60 420 60H31Q9 60 6 40Z" fill="var(--navy)"/>
    </svg>
    <div class="brand on-dark"><span class="mark"></span><span>Fenwick Ridge Accounting</span></div>
  </section>

  <section class="sheet card-front" aria-label="Business card front">
    <div class="brand"><span class="mark"></span><span>Fenwick<br>Ridge<br>Accounting</span></div>
    <div class="person"><b>LENA MORROW</b><span>General Manager</span></div>
    <div class="contact">
      <div class="row"><svg viewBox="0 0 10 10"><path d="M2 0h2l1 3-1.5 1a6 6 0 0 0 2.5 2.5L7 5l3 1v2a2 2 0 0 1-2 2A8 8 0 0 1 0 2a2 2 0 0 1 2-2z"/></svg>555-014-2290</div>
      <div class="row"><svg viewBox="0 0 10 10"><path d="M0 2h10v6H0z"/></svg>info@fenwickridge.com</div>
      <div class="row"><svg viewBox="0 0 10 10"><circle cx="5" cy="5" r="5"/></svg>www.fenwickridge.com</div>
    </div>
    <div class="office">Level 12, Keel Tower<br>18 Quay Lane, Sydney</div>
    <svg class="stripe" width="167" height="4" viewBox="0 0 167 4" preserveAspectRatio="none" aria-hidden="true">
      <polygon points="0,0 81,0 77,4 0,4" fill="var(--sky)"/>
      <polygon points="84,0 167,0 167,4 80,4" fill="var(--navy)"/>
    </svg>
  </section>

  <section class="sheet card-back" aria-label="Business card back">
    <div class="brand on-dark"><span class="mark"></span><span>Fenwick<br>Ridge<br>Accounting</span></div>
  </section>

</main>
</body>
</html>
```